Velk Consulting -New consulting business in architecture, urban planning, and real estate development

We need a stationery design, including logo, business cards, etc, work for a new consulting business that works in the world of architectural, urban planning and real estate development.

The name of the company is "Velk Consulting". Velk is my last name but it of course also has the meaning 'cool' and 'hip'.

Target Market(s)

The business will provide boutique consulting services to high end clients that may include property developers, cities, etc.

Industry/Entity Type

Consultant

Contact Information for Business Card

VELK Consulting
First Name Last Name
Title
Phone number
Address
Website
Optional: Twitter handle

Logo Text

VELK Consulting

Font styles to use
Sans Serif

Colors

Designer to choose colors to be used in the design.

Requirements
Must have
• Simple design
• Easy to read font
• Modern
• Elegance
• Nice font that can be used for future reports, letters, etc.
• Good colour scheme that allows for the elegance to come through
Should not have
• Complex design ideas
• Complex logos
• Not a corporate feel and look

```html
<!DOCTYPE html>
<html lang="en">
<head>
<meta charset="utf-8">
<title>Velk Consulting – Envelopes</title>
<link rel="stylesheet" href="https://fonts.googleapis.com/css2?family=Josefin+Sans:wght@400;600&family=Montserrat:wght@400;600&display=swap">
<style>
  :root {
    --backdrop: #c9dbe1;
    --paper: #f3f3f5;
    --paper-shade: #e4e4e8;
    --flap-inside: #c6c6ca;
    --gold: #b0902f;
    --gold-light: #c3a45a;
    --ink: #2b2b2b;
    --white: #ffffff;
  }
  * { margin: 0; padding: 0; box-sizing: border-box; }
  html, body { width: 1200px; height: 1052px; overflow: hidden; }
  body {
    position: relative;
    background: var(--backdrop);
    font-family: "Montserrat", sans-serif;
  }
  .envelope { position: absolute; }
  .envelope--back { left: 69px; top: 336px; width: 484px; height: 327px; }
  .envelope--back svg { position: absolute; inset: 0; }
  .envelope--front { left: 630px; top: 416px; width: 490px; height: 245px; }
  .envelope__pattern {
    position: absolute; inset: 0;
    background: radial-gradient(ellipse at 55% 50%, var(--gold-light) 0%, var(--gold) 70%);
  }
  .wordmark {
    position: absolute;
    font-family: "Josefin Sans", sans-serif;
    font-weight: 600;
    text-align: center;
    line-height: 1;
  }
  .wordmark__name { display: block; font-size: 52px; letter-spacing: 1px; }
  .wordmark__sub { display: block; font-size: 10px; letter-spacing: 4px; margin-top: 6px; }
  .wordmark--gold { color: var(--gold); left: 194px; top: 198px; width: 100px; }
  .wordmark--gold .wordmark__sub { color: var(--ink); }
  .wordmark--white { color: var(--white); left: 28px; top: 30px; text-align: left; }
  .contact {
    position: absolute; left: 28px; top: 198px;
    color: var(--white); font-size: 6.5px; letter-spacing: .2px;
  }
  .contact__address b { font-weight: 600; }
  .contact__lines { display: flex; align-items: center; margin-top: 9px; }
  .contact__item { display: flex; align-items: center; gap: 4px; padding-right: 8px; margin-right: 8px; border-right: 1px solid rgba(255,255,255,.5); }
  .contact__item:last-child { border-right: 0; }
  .contact__item svg { width: 8px; height: 8px; }
</style>
</head>
<body>
  <div class="envelope envelope--back">
    <svg viewBox="0 0 484 327" width="484" height="327">
      <polygon points="22,0 460,0 484,84 0,84" fill="var(--flap-inside)"/>
      <rect x="0" y="84" width="484" height="243" fill="var(--paper)"/>
      <polyline points="0,84 160,185" fill="none" stroke="var(--paper-shade)" stroke-width="1.5"/>
      <polyline points="484,84 430,135" fill="none" stroke="var(--paper-shade)" stroke-width="1.5"/>
      <polygon points="28,134 450,134 484,327 0,327" fill="var(--paper)" stroke="var(--paper-shade)" stroke-width="1.5"/>
    </svg>
    <div class="wordmark wordmark--gold">
      <span class="wordmark__name">VELK</span>
      <span class="wordmark__sub">CONSULTING</span>
    </div>
  </div>

  <div class="envelope envelope--front">
    <div class="envelope__pattern" role="img" aria-label="Gold envelope face with a tone-on-tone mandala ornament pattern"></div>
    <div class="wordmark wordmark--white">
      <span class="wordmark__name">VELK</span>
      <span class="wordmark__sub">CONSULTING</span>
    </div>
    <div class="contact">
      <p class="contact__address"><b>Velk Consulting</b> - 214 N Harbor Avenue, Alder Falls, OR 97310</p>
      <div class="contact__lines">
        <span class="contact__item">
          <svg viewBox="0 0 10 10"><path d="M2 1l2 0 1 2-1.2 1a5 5 0 0 0 2.2 2.2L7 5l2 1v2c0 .6-.4 1-1 1A8 8 0 0 1 1 2c0-.6.4-1 1-1z" fill="var(--white)"/></svg>
          000 000 0000
        </span>
        <span class="contact__item">
          <svg viewBox="0 0 10 10"><rect x=".5" y="2" width="9" height="6" fill="none" stroke="var(--white)" stroke-width=".8"/><polyline points=".5,2 5,5.5 9.5,2" fill="none" stroke="var(--white)" stroke-width=".8"/></svg>
          info@velkconsulting.com
        </span>
        <span class="contact__item">
          <svg viewBox="0 0 10 10"><circle cx="5" cy="5" r="4.3" fill="none" stroke="var(--white)" stroke-width=".8"/><ellipse cx="5" cy="5" rx="1.8" ry="4.3" fill="none" stroke="var(--white)" stroke-width=".7"/><line x1=".7" y1="5" x2="9.3" y2="5" stroke="var(--white)" stroke-width=".7"/></svg>
          www.velkconsulting.com
        </span>
      </div>
    </div>
  </div>
</body>
</html>
```